The Linen Loft Co

We need a business card design for our wardrobe company.
Please visit our website www.gentlelinenlofts.com to get an idea of who we are.

```html
<!DOCTYPE html>
<html lang="en">
<head>
<meta charset="utf-8">
<title>The Linen Loft Co — Business Card</title>
<link rel="stylesheet" href="https://fonts.googleapis.com/css2?family=Oswald:wght@500&family=Roboto:wght@400&display=swap">
<style>
  :root {
    --backdrop-light: #2e2e2e;
    --backdrop-dark: #0b0b0b;
    --card: #1d1d1d;
    --card-sheen: #2a2a2a;
    --ink: #f2f2f2;
    --ink-soft: #d9d9d9;
    --emboss: #8a8a8a;
    --emboss-dark: #141414;
  }
  * { margin: 0; padding: 0; box-sizing: border-box; }
  html, body { width: 1200px; height: 900px; overflow: hidden; }
  body {
    background: radial-gradient(ellipse at 50% 30%, var(--backdrop-light), var(--backdrop-dark) 75%);
    font-family: "Roboto", Arial, sans-serif;
    position: relative;
  }
  .card {
    position: absolute;
    left: 270px;
    width: 660px;
    height: 377px;
    background: linear-gradient(160deg, var(--card) 45%, var(--card-sheen) 75%, var(--card) 100%);
    box-shadow: 0 18px 40px rgba(0,0,0,0.6);
  }
  .card--front { top: 62px; }
  .card--back { top: 462px; }

  /* Front */
  .brand {
    position: absolute;
    left: 160px;
    top: 140px;
    display: flex;
    align-items: center;
    gap: 24px;
  }
  .brand__mark {
    width: 70px;
    height: 70px;
    background: var(--emboss-dark);
  }
  .brand__name {
    font-size: 21px;
    letter-spacing: 1.5px;
    text-transform: uppercase;
    color: var(--emboss);
  }
  .brand__tagline {
    margin-top: 6px;
    margin-left: 20px;
    font-size: 17px;
    letter-spacing: 1px;
    color: var(--emboss);
  }

  /* Back */
  .person {
    position: absolute;
    right: 370px;
    top: 145px;
    text-align: right;
    color: var(--ink);
  }
  .person__name {
    font-family: "Oswald", "Arial Narrow", sans-serif;
    font-weight: 500;
    font-size: 38px;
    letter-spacing: 1px;
    line-height: 1;
    text-transform: uppercase;
  }
  .person__role {
    margin-top: 10px;
    margin-right: 14px;
    font-size: 17px;
    color: var(--ink-soft);
  }
  .divider {
    position: absolute;
    left: 310px;
    top: 150px;
    width: 1.5px;
    height: 66px;
    background: var(--ink-soft);
  }
  .contacts {
    position: absolute;
    left: 330px;
    top: 148px;
    list-style: none;
    color: var(--ink);
    font-size: 18px;
    letter-spacing: 0.5px;
  }
  .contacts li {
    display: flex;
    align-items: center;
    gap: 10px;
    height: 24px;
  }
  .contacts svg { width: 14px; height: 14px; flex: none; }
  .address {
    position: absolute;
    left: 0;
    right: 0;
    top: 318px;
    text-align: center;
    font-size: 18px;
    letter-spacing: 0.5px;
    color: var(--ink);
  }
</style>
</head>
<body>

<section class="card card--front" aria-label="Card front">
  <div class="brand">
    <div class="brand__mark"></div>
    <div>
      <p class="brand__name">The Linen Loft Co</p>
      <p class="brand__tagline">Folded with quiet Care</p>
    </div>
  </div>
</section>

<section class="card card--back" aria-label="Card back">
  <div class="person">
    <p class="person__name">Daniel Harlow</p>
    <p class="person__role">Director</p>
  </div>
  <div class="divider"></div>
  <ul class="contacts">
    <li>
      <svg viewBox="0 0 16 16" fill="none" stroke="currentColor" stroke-width="1.4" aria-hidden="true">
        <path d="M4 1.5h2.5l1 3.5-1.7 1.2a8 8 0 0 0 4 4L11 8.5l3.5 1V12a2 2 0 0 1-2 2A11 11 0 0 1 2 3.5a2 2 0 0 1 2-2z"/>
      </svg>
      0207 555 0148
    </li>
    <li>
      <svg viewBox="0 0 16 16" fill="none" stroke="currentColor" stroke-width="1.4" aria-hidden="true">
        <rect x="1.5" y="3.5" width="13" height="9"/>
        <path d="M1.5 3.5 8 9l6.5-5.5"/>
      </svg>
      info@gentlelinenlofts.com
    </li>
    <li>
      <svg viewBox="0 0 16 16" fill="none" stroke="currentColor" stroke-width="1.2" aria-hidden="true">
        <circle cx="8" cy="8" r="6.5"/>
        <ellipse cx="8" cy="8" rx="3" ry="6.5"/>
        <path d="M1.5 8h13M2.5 4.8h11M2.5 11.2h11"/>
      </svg>
      www.gentlelinenlofts.com
    </li>
  </ul>
  <p class="address">Harbour Court, 42 Mill Lane, London N1 7QB</p>
</section>

</body>
</html>
```